Chimney Service company needs new business card design

We need a updated business card with our new logo added. We provide a full range of chimney services throughout Vermont and New Hampshire. The business card will be one sided and color. Attached is our current business card another document showing all the information we would like on the card.
We dont like a lot of flashy colors.... here is a link to our website to get an idea of our branding www.flueguardianvt.example

Target Market(s)

homeowners

Industry/Entity Type

Business

Contact Information for Business Card

See attached sheet for content.

Font styles to use
Serif
Sans Serif

Requirements
Must have
• all information provided on separate sheet
Should not have
• Additional information that may clogg up design

```html
<!DOCTYPE html>
<html lang="en">
<head>
<meta charset="utf-8">
<title>Flue Guardian – Business Card</title>
<link href="https://fonts.googleapis.com/css2?family=Exo+2:wght@700&family=Roboto:wght@400&display=swap" rel="stylesheet">
<style>
  :root{
    --brand-red:#8c0a0a;
    --charcoal:#333333;
    --card-light:#f3f3f3;
    --card-shade:#dedede;
    --ink:#3a3a3a;
    --white:#ffffff;
    --backdrop:#c4c4c4;
  }
  *{box-sizing:border-box;margin:0;padding:0}
  html,body{width:1200px;height:576px;overflow:hidden;background:var(--backdrop)}
  body{position:relative;font-family:"Roboto",Arial,sans-serif}

  .card{position:absolute;top:138px;width:486px;height:294px;border-radius:14px;overflow:hidden;
        background:linear-gradient(160deg,var(--card-light),var(--card-shade));
        box-shadow:0 4px 10px rgba(0,0,0,.25)}
  .card--front{left:80px}
  .card--back{left:602px;width:480px}
  .card__shape{position:absolute;inset:0}

  /* front */
  .brand-name{position:absolute;top:42px;left:0;right:0;text-align:center;
              font-family:"Roboto",Arial,sans-serif;font-weight:400;font-size:27px;line-height:32px;
              letter-spacing:1px;color:var(--white)}

  .services{position:absolute;top:160px;left:12px;right:12px;display:flex;justify-content:space-between}
  .service{flex:1;display:flex;flex-direction:column;align-items:center;border-left:1px solid var(--brand-red)}
  .service:first-child{border-left:none}
  .service__icon{width:40px;height:44px;border-radius:3px;background:linear-gradient(180deg,#a83232,#7e1010);opacity:.85}
  .service__label{margin-top:14px;font-size:11.3px;line-height:14px;color:var(--ink);text-align:center}

  .front-web{position:absolute;top:266px;left:0;right:0;display:flex;justify-content:center;align-items:center;gap:10px;
             font-size:11.5px;line-height:14px;color:var(--ink)}
  .front-web::before,.front-web::after{content:"";width:94px;height:2px;background:var(--brand-red)}

  /* back */
  .headline{position:absolute;left:24px;top:26px;font-family:"Exo 2",Arial,sans-serif;font-weight:700;
            font-size:17.5px;line-height:21px;letter-spacing:.3px;color:var(--white)}
  .since{position:absolute;left:24px;top:70px;width:162px;display:flex;align-items:center;gap:6px;
         font-size:8.5px;line-height:10px;color:var(--white)}
  .since::before,.since::after{content:"";flex:1;height:1px;background:var(--white)}

  .contacts{position:absolute;left:26px;top:164px;list-style:none}
  .contacts li{display:flex;align-items:center;gap:10px;height:19.5px;font-size:12px;color:var(--white)}
  .contacts svg{width:11px;height:11px}

  .perks{position:absolute;left:26px;top:237px;list-style:none}
  .perks li{font-size:11.3px;line-height:15.5px;color:var(--white)}
  .perks li::before{content:"» "}

  .back-name{position:absolute;left:310px;right:10px;top:122px;text-align:center;
             font-family:"Roboto",Arial,sans-serif;font-weight:400;font-size:24px;line-height:28px;
             letter-spacing:1px;color:var(--charcoal)}
</style>
</head>
<body>

<section class="card card--front">
  <svg class="card__shape" viewBox="0 0 486 294" preserveAspectRatio="none" aria-hidden="true">
    <path d="M0 104 Q243 148 486 104 L486 122 Q243 168 0 108 Z" fill="var(--charcoal)"/>
    <path d="M0 0 H486 V104 Q243 150 0 100 Z" fill="var(--brand-red)"/>
  </svg>
  <p class="brand-name">FLUE GUARDIAN</p>
  <div class="services">
    <div class="service"><span class="service__icon" role="img" aria-label="Masonry chimney icon"></span><p class="service__label">Full Masonry<br>Services</p></div>
    <div class="service"><span class="service__icon" role="img" aria-label="Brick restoration icon"></span><p class="service__label">Historic Chimney<br>Restoration</p></div>
    <div class="service"><span class="service__icon" role="img" aria-label="Steel liner icon"></span><p class="service__label">Stainless<br>Steel Liners</p></div>
    <div class="service"><span class="service__icon" role="img" aria-label="Bricks and trowel icon"></span><p class="service__label">New Chimney<br>Installations</p></div>
    <div class="service"><span class="service__icon" role="img" aria-label="Chimney sweep brush icon"></span><p class="service__label">FSTB Certified<br>Chimney sweeps</p></div>
  </div>
  <p class="front-web">www.flueguardianvt.example</p>
</section>

<section class="card card--back">
  <svg class="card__shape" viewBox="0 0 480 294" preserveAspectRatio="none" aria-hidden="true">
    <path d="M0 0 H316 Q270 150 304 294 H0 Z" fill="var(--charcoal)"/>
    <path d="M0 0 H304 Q260 150 296 294 H0 Z" fill="var(--brand-red)"/>
    <path d="M0 230 H272 Q276 252 284 274 H0 Z" fill="var(--charcoal)"/>
  </svg>
  <h1 class="headline">SERVING VT AND<br>NEW HAMPSHIRE</h1>
  <p class="since">SINCE 1989</p>
  <ul class="contacts">
    <li><svg viewBox="0 0 12 12"><path d="M2 1h3l1 3-2 1a7 7 0 0 0 3 3l1-2 3 1v3c-6 0-9-3-9-9z" fill="var(--white)"/></svg>802-555-0147</li>
    <li><svg viewBox="0 0 12 12"><rect x="1" y="2.5" width="10" height="7" fill="none" stroke="var(--white)"/><path d="M1 2.5l5 4 5-4" fill="none" stroke="var(--white)"/></svg>info@flueguardianvt.example</li>
    <li><svg viewBox="0 0 12 12"><circle cx="6" cy="6" r="5" fill="none" stroke="var(--white)"/><ellipse cx="6" cy="6" rx="2" ry="5" fill="none" stroke="var(--white)"/><path d="M1 6h10" stroke="var(--white)"/></svg>www.flueguardianvt.example</li>
  </ul>
  <ul class="perks">
    <li>Fully Insured – Free Estimates</li>
    <li>Family Owned &amp; Operated</li>
  </ul>
  <p class="back-name">FLUE<br>GUARDIAN</p>
</section>

</body>
</html>
```